Heating and Cooling Company mobile website

We need a website specifically designed for a viewing on a mobile device.

We serve the northern New Jersey heating, cooling and electrical residential market.

The goal is the drive traffic to the site by using Brintel Pay Per click. People will be searching for an HVAC contractor, and they land on our page. They need to get key info quickly without all the clutter of a desktop type of site.

Target Market(s)

Homeowners

Industry/Entity Type

Hvac

Coding

Coded - Design and coding required

Number of Pages Required

5+ page

Font styles to use
Serif

Requirements
Must have
• View attachments to see samples of the desktop version. It must have a similar color scheme
• The copy of the website is also attached
Nice to have
• Would like it to have a sort of Vardok feel to it. Make it seem like its an app that people are using and that its exciting to be on the website. It would be nice to have a page where customers can book appointments

```html
<!DOCTYPE html>
<html lang="en">
<head>
<meta charset="utf-8">
<title>Hearthway Climate — Heating &amp; Cooling</title>
<link href="https://fonts.googleapis.com/css2?family=Montserrat:wght@400;500;600;700&display=swap" rel="stylesheet">
<style>
:root{
  --crimson:#981b32;
  --ink:#1c1c1c;
  --beige:#f1ede7;
  --white:#ffffff;
  --line:#dcdcdc;
}
*{box-sizing:border-box;margin:0;padding:0}
html,body{width:1200px;height:5373px;overflow:hidden}
body{font-family:'Montserrat',sans-serif;color:var(--ink);background:var(--white);position:relative}
.abs{position:absolute}
.header{left:0;top:0;width:1200px;height:161px;background:var(--white);box-shadow:0 4px 10px rgba(0,0,0,.08);z-index:2}
.quick-call{left:36px;top:56px;display:flex;align-items:center;gap:22px;font-weight:600;font-size:40px}
.menu{right:36px;top:48px;display:flex;align-items:center;gap:22px;font-weight:600;font-size:40px}
.menu-btn{width:68px;height:62px;background:var(--crimson);border-radius:8px;display:flex;flex-direction:column;justify-content:center;align-items:center;gap:7px}
.menu-btn span{width:28px;height:5px;background:var(--white)}
.brand{left:420px;width:360px;height:226px;display:flex;flex-direction:column;justify-content:center;align-items:center;text-align:center;color:var(--crimson);font-weight:700;font-size:50px;line-height:1.05;z-index:3}
.brand-mark{width:34px;height:34px;background:var(--crimson);border-radius:50%;margin-bottom:14px}
.hero{left:0;top:161px;width:1200px;height:1118px;background:var(--beige)}
.eyebrow{left:0;width:1200px;top:355px;text-align:center;color:var(--crimson);font-weight:700;font-size:34px}
.hero-title{left:0;width:1200px;top:410px;text-align:center;font-weight:500;font-size:64px;line-height:72px}
.van{left:233px;top:591px;width:842px;height:430px;border-radius:40px;background:linear-gradient(180deg,#3a2a2a 0%,#151515 70%,#bdb6ad 100%)}
.arrow{top:780px;font-size:54px;font-weight:700}
.book{left:433px;top:1039px;width:334px;height:93px;background:var(--crimson);color:var(--white);font-weight:700;font-size:38px;display:flex;align-items:center;justify-content:center}
.section-title{left:0;width:1200px;text-align:center;font-weight:700;font-size:48px}
.badge{left:358px;width:484px;height:312px}
.badge-shape{position:absolute;left:0;top:0;width:484px;height:312px}
.badge-icon{position:absolute;left:182px;top:38px;width:120px;height:120px}
.badge-label{position:absolute;left:0;width:484px;top:172px;text-align:center;color:var(--white);font-weight:700;font-size:38px}
.news{left:0;top:3224px;width:1200px;height:1547px;background:var(--beige)}
.news-photo{left:39px;top:3457px;width:1122px;height:619px;border:10px solid var(--white);background:linear-gradient(135deg,#f4f4f4 0%,#dfe3e6 45%,#b9d3e6 70%,#eceae6 100%)}
.news-date{left:0;width:1200px;top:4140px;text-align:center;font-weight:700;font-size:50px}
.news-text{left:0;width:1200px;top:4212px;text-align:center;font-size:44px;line-height:74px;white-space:nowrap}
.footer{left:0;top:4771px;width:1200px;height:602px;background:var(--white)}
.social{left:0;width:1200px;top:4970px;display:flex;justify-content:center;gap:40px}
.social span{width:38px;height:38px;border-radius:50%;background:var(--crimson)}
.quick-links{left:36px;top:5065px;width:1128px;height:154px;border:2px solid var(--line);background:#f7f7f7;display:flex;align-items:center;justify-content:space-between;padding:0 44px 0 36px;font-weight:700;font-size:50px}
.copyright{left:0;width:1200px;top:5278px;text-align:center;font-weight:700;font-size:32px}
</style>
</head>
<body>
<header class="abs header">
  <div class="abs quick-call">
    <svg width="34" height="34" viewBox="0 0 24 24"><path fill="#981b32" d="M6.6 10.8c1.4 2.8 3.8 5.1 6.6 6.6l2.2-2.2c.3-.3.7-.4 1-.2 1.1.4 2.3.6 3.6.6.6 0 1 .4 1 1V20c0 .6-.4 1-1 1C10.6 21 3 13.4 3 4c0-.6.4-1 1-1h3.5c.6 0 1 .4 1 1 0 1.3.2 2.5.6 3.6.1.3 0 .7-.2 1z"/></svg>
    QUICK CALL
  </div>
  <div class="abs menu">MENU <div class="menu-btn"><span></span><span></span><span></span></div></div>
</header>
<div class="abs brand" style="top:54px"><div class="brand-mark"></div>Hearthway<br>Climate</div>

<section class="abs hero"></section>
<div class="abs eyebrow">HEARTHWAY CLIMATE</div>
<h1 class="abs hero-title">Most Trusted &amp;<br>Cooling Company</h1>
<div class="abs van" role="img" aria-label="Company service van in black with branded livery"></div>
<div class="abs arrow" style="left:56px">&#8249;</div>
<div class="abs arrow" style="left:1106px">&#8250;</div>
<a class="abs book">BOOK NOW</a>

<h2 class="abs section-title" style="top:1388px">OUR SERVICES</h2>

<div class="abs badge" style="top:1497px">
  <svg class="badge-shape" viewBox="0 0 484 312"><path fill="#981b32" d="M0 20 Q242 -12 484 20 L452 70 L452 190 Q452 262 242 312 Q32 262 32 190 L32 70 Z"/></svg>
  <svg class="badge-icon" viewBox="0 0 120 120"><circle cx="60" cy="60" r="34" fill="#fff"/><g stroke="#fff" stroke-width="5"><line x1="60" y1="4" x2="60" y2="16"/><line x1="60" y1="104" x2="60" y2="116"/><line x1="4" y1="60" x2="16" y2="60"/><line x1="104" y1="60" x2="116" y2="60"/><line x1="20" y1="20" x2="29" y2="29"/><line x1="91" y1="91" x2="100" y2="100"/><line x1="100" y1="20" x2="91" y2="29"/><line x1="29" y1="91" x2="20" y2="100"/></g></svg>
  <div class="badge-label">HEATING</div>
</div>
<div class="abs badge" style="top:1898px">
  <svg class="badge-shape" viewBox="0 0 484 312"><path fill="#981b32" d="M0 20 Q242 -12 484 20 L452 70 L452 190 Q452 262 242 312 Q32 262 32 190 L32 70 Z"/></svg>
  <svg class="badge-icon" viewBox="0 0 120 120"><g stroke="#fff" stroke-width="7" stroke-linecap="round"><line x1="60" y1="8" x2="60" y2="112"/><line x1="15" y1="34" x2="105" y2="86"/><line x1="105" y1="34" x2="15" y2="86"/><polyline fill="none" points="46,14 60,28 74,14"/><polyline fill="none" points="46,106 60,92 74,106"/></g></svg>
  <div class="badge-label">AIR CONDITIONING</div>
</div>
<div class="abs badge" style="top:2328px">
  <svg class="badge-shape" viewBox="0 0 484 312"><path fill="#981b32" d="M0 20 Q242 -12 484 20 L452 70 L452 190 Q452 262 242 312 Q32 262 32 190 L32 70 Z"/></svg>
  <svg class="badge-icon" viewBox="0 0 120 120"><path fill="#fff" d="M98 10a28 28 0 0 0-30 38L14 102a10 10 0 0 0 14 14l54-54a28 28 0 0 0 38-30l-16 16-14-4-4-14z"/></svg>
  <div class="badge-label">OTHER SERVICES</div>
</div>
<div class="abs badge" style="top:2769px">
  <svg class="badge-shape" viewBox="0 0 484 312"><path fill="#981b32" d="M0 20 Q242 -12 484 20 L452 70 L452 190 Q452 262 242 312 Q32 262 32 190 L32 70 Z"/></svg>
  <svg class="badge-icon" viewBox="0 0 120 120"><circle cx="60" cy="64" r="40" fill="#fff"/><circle cx="60" cy="64" r="26" fill="#981b32"/></svg>
  <div class="badge-label">WHO WE ARE</div>
</div>

<section class="abs news"></section>
<h2 class="abs section-title" style="top:3311px">LATEST NEWS</h2>
<div class="abs news-photo" role="img" aria-label="Wall-mounted air conditioner blowing cool air into a bright room"></div>
<div class="abs news-date">FEBRUARY 21 th | 2017</div>
<p class="abs news-text">Neque porro quisquam est qui dolorem ipsum<br>quia dolor sit amet, consectetur, adipisci velit..</p>

<footer class="abs footer"></footer>
<div class="abs brand" style="top:4658px"><div class="brand-mark"></div>Hearthway<br>Climate</div>
<div class="abs social"><span></span><span></span><span></span></div>
<div class="abs quick-links">Quick Links
  <svg width="36" height="22" viewBox="0 0 36 22"><polyline points="4,4 18,18 32,4" fill="none" stroke="#981b32" stroke-width="5"/></svg>
</div>
<div class="abs copyright">© 2017 COMPANY NAME | ALL RIGHTS RESERVED</div>
</body>
</html>
```